Business Card Design for Vintage Jazz

I am a vintage jazz band leader in New York City. My groups play the music of the 1920s, 1930s and 1940s. My website is morvalquist.com for more info on what I do.

I am looking for a two sided business card design that has the look and feel of a really nice business card from the 1930s. I need to convey with the design that my work has that vintage kind of class and style, but also conveys that we are fun and entertaining.

Most importantly it should make a bold staement. If Hal Denbrook had a card, what would it have looked like? I want a card that I feel confident will make an impact and will let people know that my work is te the top that NYC has to offer in vintage jazz..

Note that I have only decided to avoid the "committed payment" option as I have not used this service before. Assuming that I get quality work I will select a design from those presented.

Target Market(s)

people who want to hire my band for events, media, and new fans of the band

Industry/Entity Type

Performing Art

Contact Information for Business Card

Definitely a matte finish, possibly a sort of old style of paper with that brown tint? definitely a thick card.

Requirements
Must have
• FRONT
• My name: Tobin Vashley
• What I do: Bandleader, Guitarist, Vocalist, Songwriter
• Contact Details: morvalquist.com tobin@morvalquist.com 646-555-0148
• BACK
• My Social Media Links:
• facebook.morvalquist.com
• twitter, instagram, linkedin: morvalquist
• I'm also including a photo image I would like to use. The photo's background is not needed, and to be honest isn't really desireable. Just looking to use the image of me.
Nice to have
• I'm attaching which could be used as is, omitted from the card, or altered maybe with text going around the outside of the circle or in some other way. It may need some clean up to the edges of the lettering as we only use it for the website thumbnail.
• If there's space I'd like to include the text "join our mailing list for a free song download: freesong.morvalquist.com" If not perhaps just "Download a Free Song at: freesong.morvalquist.com - something to this end.
Should not have
• anything cartoony. Don't think retro 90s's vision of the swing era, think actual swing era!
• anything modern. Got to look old school
• Try to avoid dark backgrounds. Since we often play in bars and clubs where it is dar, a d
• avoid script fonts.

```html
<!DOCTYPE html>
<html lang="en">
<head>
<meta charset="utf-8">
<title>Tobin Vashley — Business Card</title>
<link rel="stylesheet" href="https://fonts.googleapis.com/css2?family=Source+Sans+3:ital,wght@0,400;0,600;1,400;1,600&display=swap">
<style>
  :root {
    --backdrop: #2b2b2b;
    --card: #ffffff;
    --ink: #111111;
    --band: #000000;
    --text-grey: #444444;
    --rule: #222222;
    --photo-light: #8a8a8a;
    --photo-dark: #1e1e1e;
  }
  * { margin: 0; padding: 0; box-sizing: border-box; }
  html, body { width: 1200px; height: 886px; overflow: hidden; }
  body {
    position: relative;
    background: var(--backdrop);
    font-family: "Source Sans 3", "Myriad Pro", sans-serif;
    color: var(--ink);
  }
  .card {
    position: absolute;
    width: 566px;
    height: 323px;
    background: var(--card);
    border-radius: 15px;
    overflow: hidden;
    box-shadow: 0 4px 14px rgba(0,0,0,0.45);
  }
  .card--front { left: 315px; top: 102px; }
  .card--back  { left: 312px; top: 460px; }

  /* Front */
  .name-band {
    position: absolute;
    left: 0; top: 58px;
    width: 100%; height: 96px;
    background: var(--band);
  }
  .identity {
    position: absolute;
    left: 38px; top: 71px;
    color: #fff;
  }
  .identity__name { font-size: 21px; font-weight: 600; line-height: 26px; }
  .identity__role { font-size: 16px; font-weight: 400; line-height: 21px; }
  .portrait {
    position: absolute;
    right: 0; top: 0;
    width: 300px; height: 323px;
    background: linear-gradient(160deg, var(--photo-light) 0%, #4a4a4a 45%, var(--photo-dark) 100%);
    clip-path: polygon(22% 18%, 45% 0, 78% 8%, 100% 30%, 100% 100%, 8% 100%, 4% 60%);
  }
  .contact {
    position: absolute;
    left: 38px; top: 240px;
    list-style: none;
  }
  .contact li {
    display: flex;
    align-items: center;
    height: 22px;
    font-size: 16px;
    color: var(--text-grey);
  }
  .contact svg { width: 14px; height: 14px; margin-right: 8px; flex: none; }

  /* Back */
  .brand {
    position: absolute;
    left: 0; top: 90px;
    width: 100%;
    display: flex;
    justify-content: center;
    align-items: center;
    gap: 16px;
  }
  .brand__mark { width: 72px; height: 72px; border-radius: 50%; background: var(--band); }
  .brand__name { font-size: 30px; font-weight: 600; color: var(--ink); letter-spacing: 0.5px; }
  .back-rule {
    position: absolute;
    left: 31px; top: 240px;
    width: 505px; height: 1px;
    background: var(--rule);
  }
  .social {
    position: absolute;
    left: 32px; top: 252px;
    list-style: none;
  }
  .social li {
    display: flex;
    align-items: center;
    height: 27px;
    font-size: 16px;
    color: var(--text-grey);
  }
  .social__dot {
    width: 21px; height: 21px;
    border-radius: 50%;
    background: var(--band);
    margin-right: 7px;
    flex: none;
  }
  .free-song {
    position: absolute;
    right: 30px; top: 258px;
    text-align: right;
    font-style: italic;
    font-size: 16px;
    line-height: 20px;
    color: var(--text-grey);
  }
  .free-song strong { font-weight: 600; }
</style>
</head>
<body>

<section class="card card--front">
  <div class="name-band"></div>
  <div class="identity">
    <div class="identity__name">Tobin Vashley</div>
    <div class="identity__role">Bandleader, Guitarist</div>
    <div class="identity__role">Vocalist, Songwriter</div>
  </div>
  <div class="portrait" role="img" aria-label="Black and white photo of the bandleader in a striped blazer tipping a straw boater hat"></div>
  <ul class="contact">
    <li>
      <svg viewBox="0 0 14 14"><rect x="3" y="0.5" width="8" height="13" rx="1.5" fill="var(--ink)"/><rect x="4.5" y="2" width="5" height="8.5" fill="#fff"/></svg>
      646-555-0148
    </li>
    <li>
      <svg viewBox="0 0 14 14"><rect x="1" y="3" width="12" height="8" fill="var(--ink)"/><path d="M1.5 3.5 L7 8 L12.5 3.5" stroke="#fff" stroke-width="1.2" fill="none"/></svg>
      tobin@morvalquist.com
    </li>
    <li>
      <svg viewBox="0 0 14 14"><circle cx="7" cy="7" r="6" fill="var(--ink)"/><ellipse cx="7" cy="7" rx="2.6" ry="6" stroke="#fff" stroke-width="1" fill="none"/><line x1="1" y1="7" x2="13" y2="7" stroke="#fff" stroke-width="1"/></svg>
      morvalquist.com
    </li>
  </ul>
</section>

<section class="card card--back">
  <div class="brand">
    <span class="brand__mark"></span>
    <span class="brand__name">Tobin Vashley</span>
  </div>
  <div class="back-rule"></div>
  <ul class="social">
    <li><span class="social__dot"></span>morvalquist.com</li>
    <li><span class="social__dot"></span>morvalquist</li>
  </ul>
  <p class="free-song">Download a Free Song at:<br><strong>freesong.morvalquist.com</strong></p>
</section>

</body>
</html>
```